Beyond Home Ground Stand Out, Step In

Need a book cover for my new book. Book cover will also be used as a banner for a web site I am creating so whatever I choose as a book cover hopefully will also look good on my website. I'm a career advisor. My book is aimed at international students who come to the U.S to go to college and try to secure employment in the U.S after graduation. This process is very challenging for students. Need a creative cover that communicates the message of my book in a non-boring way but yet in a clear way. Attached is the cover I have right now. Not too too happy with it. Seems boring and obvious but it does communicate what my book is all about. Good project for those who are globally minded and have lived or studies overseas. My title of my book captures the essence of my project: basically I am saying that it is an advnatage to be a foreigner because you can get noticed by your unique traits and skills and get hired.

Reason: Hi. I'd like designers to submit a book jacket design - I did not make that clear - and I will be trying to make a decision in the next 5 days. Also, I have a picture that can be used for a about the author piece. Designers: please remember that the design needs to get international students who are going to college in the U.S excited about buying the book. The book needs to convey success and the idea that being different/international can help them get hired. But we need to do that in a clever and creative way, not in a predicable way. Thank you so munch for your patience and I will provide feedback this coming week and will be deciding soon. You are all very talented.

Target Market(s)

International students who come to college in the United States. Ages range from 19 to 28 years old. Most international students are from China. India is the second country mostly represented. Many students are females.

Requirements
Must have
• A good cover will have impact and creatively translate the title of my book into a strong visual. I wanted something creative but I don't think it can be too nebulous because if it is, I may lose my audience.
Nice to have
• Book Title: Beyond Home Ground
• Subtitle: Stand out. Step in

```html
<!DOCTYPE html>
<html lang="en">
<head>
<meta charset="utf-8">
<title>Beyond Home Ground — Book Cover</title>
<link rel="stylesheet" href="https://fonts.googleapis.com/css2?family=Bebas+Neue&family=Oswald:wght@500;600&display=swap">
<style>
  :root {
    --page-bg: #f4f4f4;
    --cover-top: #ffffff;
    --cover-bottom: #e6e6e6;
    --ink: #111111;
    --accent-red: #e3101b;
    --banner-yellow: #f6d800;
    --seat-dark: #141414;
    --seat-mid: #3a3a3a;
    --chrome: #cfcfcf;
  }
  * { margin: 0; padding: 0; box-sizing: border-box; }
  html, body {
    width: 1200px;
    height: 900px;
    overflow: hidden;
    background: var(--page-bg);
  }
  .canvas {
    width: 1200px;
    height: 900px;
    display: flex;
    align-items: center;
    justify-content: center;
  }
  .book-cover {
    position: relative;
    width: 510px;
    height: 840px;
    background: linear-gradient(180deg, var(--cover-top) 0%, var(--cover-top) 35%, var(--cover-bottom) 100%);
    box-shadow: 0 6px 24px rgba(0,0,0,0.12);
    text-align: center;
    font-family: 'Bebas Neue', 'Oswald', sans-serif;
    color: var(--ink);
  }
  .title-block {
    position: absolute;
    top: 40px;
    left: 0;
    right: 0;
  }
  .title-lead {
    font-size: 46px;
    line-height: 1;
    letter-spacing: 1px;
  }
  .title-main {
    font-size: 128px;
    line-height: 0.92;
    letter-spacing: 1px;
  }
  .title-main--red { color: var(--accent-red); margin-top: 6px; }
  .title-main--black { color: var(--ink); }
  .hanging-banner {
    position: absolute;
    top: 316px;
    left: 50%;
    transform: translateX(-50%);
    width: 330px;
    height: 96px;
  }
  .banner-strings {
    position: absolute;
    inset: 0;
  }
  .subtitle-banner {
    position: absolute;
    bottom: 0;
    left: 0;
    right: 0;
    height: 54px;
    background: var(--banner-yellow);
    color: var(--accent-red);
    font-family: 'Oswald', sans-serif;
    font-weight: 600;
    font-size: 32px;
    line-height: 54px;
    text-transform: uppercase;
    letter-spacing: 0.5px;
  }
  .scene-illustration {
    position: absolute;
    top: 505px;
    left: 45px;
    right: 45px;
    height: 180px;
    background: linear-gradient(180deg, var(--seat-dark) 0%, var(--seat-mid) 45%, var(--chrome) 100%);
  }
  .author-name {
    position: absolute;
    bottom: 50px;
    left: 0;
    right: 0;
    font-family: 'Oswald', sans-serif;
    font-weight: 600;
    font-size: 40px;
    letter-spacing: 0.5px;
    text-transform: uppercase;
  }
</style>
</head>
<body>
  <main class="canvas">
    <article class="book-cover">
      <header class="title-block">
        <div class="title-lead">Beyond</div>
        <div class="title-main title-main--red">Home</div>
        <div class="title-main title-main--black">Ground</div>
      </header>

      <div class="hanging-banner">
        <svg class="banner-strings" width="330" height="96" viewBox="0 0 330 96" aria-hidden="true">
          <line x1="8" y1="0" x2="8" y2="44" stroke="#e3101b" stroke-width="2.5"/>
          <line x1="322" y1="0" x2="322" y2="44" stroke="#e3101b" stroke-width="2.5"/>
          <line x1="8" y1="0" x2="20" y2="0" stroke="#e3101b" stroke-width="2.5"/>
          <line x1="310" y1="0" x2="322" y2="0" stroke="#e3101b" stroke-width="2.5"/>
        </svg>
        <div class="subtitle-banner">Stand out. Step in</div>
      </div>

      <div class="scene-illustration" role="img" aria-label="Photograph of a row of four empty black-and-chrome waiting-room chairs, evoking candidates awaiting a job interview"></div>

      <footer class="author-name">Author’s Name</footer>
    </article>
  </main>
</body>
</html>
```